Harlow Mechanical Contractors needs a Website

Create basic website for commercial plumbing and mechanical contractor; to include pictures of works in progress and completed works, description of all services offered and geographical locations and licenses

Target Market(s)

General Contractors, Real Estate Developers, Construction Companies

Industry/Entity Type

Construction

Coding

Coded - Design and coding required

Number of Pages Required

5+ page

• See logo attached to project

Colors
0392cd

```html
<!DOCTYPE html>
<html lang="en">
<head>
<meta charset="utf-8">
<title>Harlow Mechanical Contractors</title>
<link rel="stylesheet" href="https://fonts.googleapis.com/css2?family=Oswald:wght@400;500&family=Roboto:wght@300;400;500;700&display=swap">
<style>
:root{
  --brand:#0392cd;
  --brand-dark:#0a6fa3;
  --navy:#1b4f86;
  --ink:#333;
  --muted:#8a8a8a;
  --white:#fff;
  --footer:#333333;
  --footer-bar:#2b2b2b;
  --btn-dark:#262626;
}
*{margin:0;padding:0;box-sizing:border-box}
html,body{width:1200px;height:2338px;overflow:hidden;background:var(--white)}
body{position:relative;font-family:'Roboto',sans-serif;color:var(--ink)}
.abs{position:absolute}

/* header */
.site-header{position:absolute;left:0;top:0;width:1200px;height:105px;background:var(--white)}
.brand{position:absolute;left:98px;top:30px;display:flex;align-items:center;gap:10px}
.brand-mark{width:40px;height:40px;border-radius:50%;background:var(--navy)}
.brand-name{font-size:13px;font-weight:700;line-height:14px;color:var(--navy);text-transform:uppercase;width:110px}
.top-contact{position:absolute;left:860px;top:15px;font-size:16px;display:flex;align-items:center;gap:8px;color:var(--ink)}
.top-contact .tools{margin-left:22px;font-size:11px;color:#555;display:flex;gap:10px;align-items:center}
.main-nav{position:absolute;top:49px;left:555px;height:43px;display:flex}
.main-nav a{display:block;height:43px;line-height:43px;font-size:13px;text-decoration:none;color:var(--ink);text-transform:uppercase;padding:0 20px}
.main-nav a.active{background:var(--brand);color:var(--white)}
.main-nav a.about{margin-left:29px}
.main-nav a.services{margin-left:29px}
.main-nav a.blog{margin-left:29px}
.main-nav a.contact{margin-left:29px}

/* hero */
.hero{position:absolute;left:0;top:105px;width:1200px;height:575px;background:linear-gradient(180deg,#2d5f95 0%,#6f9fc9 45%,#32506f 100%)}
.hero-arrow{position:absolute;top:232px;width:38px;height:38px}
.hero-title{position:absolute;top:380px;width:1200px;text-align:center;font-family:'Oswald',sans-serif;font-size:52px;font-weight:400;color:var(--white);text-transform:uppercase;letter-spacing:-0.5px}
.hero-sub{position:absolute;top:448px;left:240px;width:720px;text-align:center;font-size:17px;line-height:26px;color:var(--white);text-transform:uppercase}

/* welcome */
.welcome-title{position:absolute;top:720px;width:1200px;text-align:center;font-size:26px;font-weight:400;text-transform:uppercase}
.welcome-text{position:absolute;top:767px;left:155px;width:890px;text-align:center;font-size:12px;line-height:20px;color:#666}
.service{position:absolute;top:842px;width:270px;text-align:center}
.service-icon{display:block;margin:0 auto;width:150px;height:170px}
.service h3{margin-top:24px;font-size:17px;font-weight:500;color:var(--brand);text-transform:uppercase}
.service p{margin-top:10px;font-size:12px;line-height:20px;color:var(--muted)}

/* what we do */
.what-band{position:absolute;left:0;top:1161px;width:1200px;height:410px;background:var(--brand)}
.what-photo{position:absolute;left:0;top:0}
.what-title{position:absolute;left:98px;top:30px;font-size:24px;font-weight:400;color:var(--white);text-transform:uppercase}
.what-text{position:absolute;left:98px;top:76px;width:470px;font-size:12px;line-height:20px;color:var(--white)}
.what-list{position:absolute;left:98px;top:152px;list-style:none}
.what-list li{height:29px;font-size:12px;color:var(--white);text-transform:uppercase;display:flex;align-items:center;gap:10px}
.btn-dark{position:absolute;left:98px;top:336px;width:104px;height:38px;line-height:38px;text-align:center;background:var(--btn-dark);color:var(--white);font-size:11px;text-transform:uppercase}

/* customers */
.customers-title{position:absolute;top:1612px;width:1200px;text-align:center;font-size:24px;font-weight:400;text-transform:uppercase}
.customer{position:absolute;top:1693px;height:40px;display:flex;align-items:center;gap:8px;font-size:30px;font-weight:400;color:#555}
.customer .dot{width:22px;height:22px;background:#555}
.slash{position:absolute;top:1683px}

/* testimonials */
.testimonial-band{position:absolute;left:0;top:1820px;width:1200px;height:254px;background:var(--brand)}
.testimonial-title{position:absolute;top:28px;width:1200px;text-align:center;font-size:24px;font-weight:400;color:var(--white);text-transform:uppercase}
.testimonial{position:absolute;top:103px;width:520px;height:100px}
.avatar{position:absolute;left:0;top:0;width:98px;height:98px;border:3px solid var(--white);background:linear-gradient(160deg,#e8d6c8,#b89a86)}
.quote-mark{position:absolute;font-family:Georgia,serif;font-size:38px;color:#7cc3e6;line-height:1}
.quote{position:absolute;left:134px;top:6px;width:340px;font-size:11.5px;line-height:19px;color:var(--white)}
.person{position:absolute;left:134px;top:82px;font-size:12px;font-weight:700;color:var(--white);text-transform:uppercase}
.role{position:absolute;left:134px;top:100px;font-size:10px;color:var(--white);text-transform:uppercase}

/* footer */
.site-footer{position:absolute;left:0;top:2074px;width:1200px;height:206px;background:var(--footer);color:var(--white)}
.footer-col{position:absolute;top:38px}
.footer-col h4{font-size:14px;font-weight:500;text-transform:uppercase;margin-bottom:14px}
.footer-col p{font-size:11.5px;line-height:20px}
.footer-line{display:flex;align-items:center;gap:12px;margin-top:8px;font-size:14px}
.footer-line.small{font-size:12px;margin-top:6px}
.tweet{display:flex;gap:16px}
.tweet-mark{flex:none;width:16px;height:16px;background:var(--white);border-radius:2px;margin-top:3px}
.newsletter-form{display:flex;margin-top:14px}
.newsletter-form .field{width:168px;height:38px;background:var(--white);color:#555;font-size:11px;line-height:38px;padding-left:14px}
.newsletter-form .submit{width:80px;height:38px;background:var(--brand);color:var(--white);font-size:15px;line-height:38px;text-align:center}
.social{display:flex;gap:20px;margin-top:14px}
.social span{width:34px;height:34px;border-radius:3px;background:#f3f1ef}
.footer-bar{position:absolute;left:0;top:2280px;width:1200px;height:58px;background:var(--footer-bar);border-top:1px solid #444;color:var(--white);font-size:13px;text-align:center;line-height:56px}
</style>
</head>
<body>

<header class="site-header">
  <div class="brand">
    <span class="brand-mark"></span>
    <span class="brand-name">Harlow Mechanical Contractors</span>
  </div>
  <div class="top-contact">
    <svg width="16" height="16" viewBox="0 0 16 16"><rect width="16" height="16" rx="2" fill="#0392cd"/><path d="M5 3.5l2 2-1 1.3c.6 1.3 1.6 2.3 2.9 2.9l1.3-1 2 2-1.2 1.6C7.5 12 4 8.5 3.5 4.7z" fill="#fff"/></svg>
    <span>+1 555 014 2290</span>
    <span class="tools">
      <svg width="9" height="10" viewBox="0 0 9 10"><circle cx="4.5" cy="2.6" r="2.3" fill="#555"/><path d="M0 10c0-3 2-4.5 4.5-4.5S9 7 9 10z" fill="#555"/></svg>
      <span>|</span>
      <svg width="10" height="10" viewBox="0 0 10 10"><circle cx="4" cy="4" r="3" fill="none" stroke="#555" stroke-width="1.6"/><path d="M6.2 6.2L9 9" stroke="#555" stroke-width="1.8"/></svg>
    </span>
  </div>
  <nav class="main-nav">
    <a class="active" href="#">Home</a>
    <a class="about" href="#">About Us</a>
    <a class="services" href="#">Services</a>
    <a class="blog" href="#">Blog</a>
    <a class="contact" href="#">Contact</a>
  </nav>
</header>

<section class="hero" role="img" aria-label="Photograph looking up at glass office towers against a blue sky with clouds">
  <svg class="hero-arrow" style="left:60px" viewBox="0 0 38 38"><circle cx="19" cy="19" r="17" fill="none" stroke="#fff" stroke-opacity=".75" stroke-width="2"/><path d="M22 11l-8 8 8 8" fill="none" stroke="#fff" stroke-opacity=".75" stroke-width="2.4"/></svg>
  <svg class="hero-arrow" style="left:1103px" viewBox="0 0 38 38"><circle cx="19" cy="19" r="17" fill="none" stroke="#fff" stroke-opacity=".75" stroke-width="2"/><path d="M16 11l8 8-8 8" fill="none" stroke="#fff" stroke-opacity=".75" stroke-width="2.4"/></svg>
  <h1 class="hero-title">Commercial Plumbing and Mechanical</h1>
  <p class="hero-sub">Ridgeline Homes is a Canberra based building company focusing on first class residential homes and 100%</p>
</section>

<h2 class="welcome-title">Welcome Harlow Mechanical</h2>
<p class="welcome-text">There are many variations of passages of Lorem Ipsum available, but the majority have suffered alteration in some form, by injected humour, or randomised words which don't look even slightly believable. If you are going to use a passage of Lorem Ipsum, you need to be sure there isn't anything.</p>

<div class="service" style="left:90px">
  <svg class="service-icon" viewBox="0 0 150 170"><circle cx="75" cy="95" r="70" fill="#1b4f86"/></svg>
  <h3>Large Offices</h3>
  <p>Finibus Bonorum et Malorum" (The Extremes of<br>Good and Evil) by Lucan Verus, written in BC.<br>This book is a treatise</p>
</div>
<div class="service" style="left:465px">
  <svg class="service-icon" viewBox="0 0 150 170"><circle cx="75" cy="95" r="70" fill="#1b4f86"/></svg>
  <h3>Condominiums</h3>
  <p>Finibus Bonorum et Malorum" (The Extremes of<br>Good and Evil) by Lucan Verus, written in BC.<br>This book is a treatise</p>
</div>
<div class="service" style="left:840px">
  <svg class="service-icon" viewBox="0 0 150 170"><circle cx="75" cy="95" r="70" fill="#1b4f86"/></svg>
  <h3>Industrial</h3>
  <p>Finibus Bonorum et Malorum" (The Extremes of<br>Good and Evil) by Lucan Verus, written in BC.<br>This book is a treatise</p>
</div>

<section class="what-band">
  <svg class="what-photo" width="1200" height="410" viewBox="0 0 1200 410" role="img" aria-label="Photograph of a worker in an orange vest carrying grey plastic pipes in a warehouse">
    <defs><linearGradient id="whatPhoto" x1="0" y1="0" x2="1" y2="0"><stop offset="0" stop-color="#c9d3dc"/><stop offset=".6" stop-color="#d89a62"/><stop offset="1" stop-color="#7d7f86"/></linearGradient></defs>
    <polygon points="680,0 1200,0 1200,410 515,410" fill="url(#whatPhoto)"/>
  </svg>
  <h2 class="what-title">What We Do</h2>
  <p class="what-text">Denouncing pleasure and praising pain was born and I will give you a complete account of the system, and expound the actual teachings of the great explorer of the truth, the master-builder of human happiness. No one rejects, dislikes.</p>
  <ul class="what-list">
    <li><svg width="12" height="12" viewBox="0 0 12 12"><circle cx="6" cy="6" r="6" fill="#fff"/><path d="M5 3.5L7.5 6 5 8.5" fill="none" stroke="#0392cd" stroke-width="1.6"/></svg>Simulation Tools</li>
    <li><svg width="12" height="12" viewBox="0 0 12 12"><circle cx="6" cy="6" r="6" fill="#fff"/><path d="M5 3.5L7.5 6 5 8.5" fill="none" stroke="#0392cd" stroke-width="1.6"/></svg>Enterprise Intranet Systems</li>
    <li><svg width="12" height="12" viewBox="0 0 12 12"><circle cx="6" cy="6" r="6" fill="#fff"/><path d="M5 3.5L7.5 6 5 8.5" fill="none" stroke="#0392cd" stroke-width="1.6"/></svg>Hi-Tech Web Presentations</li>
    <li><svg width="12" height="12" viewBox="0 0 12 12"><circle cx="6" cy="6" r="6" fill="#fff"/><path d="M5 3.5L7.5 6 5 8.5" fill="none" stroke="#0392cd" stroke-width="1.6"/></svg>Supporting Enterprise Services</li>
    <li><svg width="12" height="12" viewBox="0 0 12 12"><circle cx="6" cy="6" r="6" fill="#fff"/><path d="M5 3.5L7.5 6 5 8.5" fill="none" stroke="#0392cd" stroke-width="1.6"/></svg>Ptimalization</li>
    <li><svg width="12" height="12" viewBox="0 0 12 12"><circle cx="6" cy="6" r="6" fill="#fff"/><path d="M5 3.5L7.5 6 5 8.5" fill="none" stroke="#0392cd" stroke-width="1.6"/></svg>Logistics Monitoring</li>
  </ul>
  <a class="btn-dark">Learn More</a>
</section>

<h2 class="customers-title">Our Customers</h2>
<div class="customer" style="left:100px"><span class="dot"></span>Northwind</div>
<svg class="slash" style="left:308px" width="52" height="60" viewBox="0 0 52 60"><path d="M50 2L2 58" stroke="#555" stroke-width="1.5"/></svg>
<div class="customer" style="left:362px"><span class="dot" style="border-radius:50%"></span>Brightway</div>
<svg class="slash" style="left:570px" width="52" height="60" viewBox="0 0 52 60"><path d="M50 2L2 58" stroke="#555" stroke-width="1.5"/></svg>
<div class="customer" style="left:628px;font-size:27px">Coastal Institute</div>
<svg class="slash" style="left:838px" width="52" height="60" viewBox="0 0 52 60"><path d="M50 2L2 58" stroke="#555" stroke-width="1.5"/></svg>
<div class="customer" style="left:892px"><span class="dot" style="border-radius:50%"></span>Postwell</div>

<section class="testimonial-band">
  <h2 class="testimonial-title">Testimonial</h2>
  <div class="testimonial" style="left:98px">
    <div class="avatar" role="img" aria-label="Portrait photo of a client"></div>
    <span class="quote-mark" style="left:110px;top:0">&ldquo;</span>
    <p class="quote">Lorem Ipsum is not simply random text. It has roots in a piece of classical Latin literature from 45 BC, making it over 2000 years old. Daniel Morrow, a Latin professor at Easton Hill College in ock, a Latin professVirginia,</p>
    <span class="quote-mark" style="left:332px;top:58px">&rdquo;</span>
    <span class="person">Martin Hale</span>
    <span class="role">CEO &amp; Architect</span>
  </div>
  <div class="testimonial" style="left:645px">
    <div class="avatar" role="img" aria-label="Portrait photo of a client"></div>
    <span class="quote-mark" style="left:110px;top:0">&ldquo;</span>
    <p class="quote">Lorem Ipsum is not simply random text. It has roots in a piece of classical Latin l in literature from 45 BC, making it over 2000 years old. Daniel Morrow, a Latin professor at Easton Hill College in ock, a Latin professVirginia,</p>
    <span class="quote-mark" style="left:370px;top:58px">&rdquo;</span>
    <span class="person" style="left:135px">Dana Whitfield</span>
    <span class="role" style="left:135px">Architect</span>
  </div>
</section>

<footer class="site-footer">
  <div class="footer-col" style="left:98px">
    <h4>Contact Us</h4>
    <p>42 Quarry Lane 3rd Floor<br>Harlow Bay, HB 20417, UK</p>
    <div class="footer-line"><svg width="16" height="16" viewBox="0 0 16 16"><path d="M3 1.5l3 3-1.4 1.8c.9 2 2.3 3.4 4.1 4.1L10.5 9l3 3-1.8 2.3C6.5 13.5 2.5 9.5 1.5 4z" fill="none" stroke="#fff" stroke-width="1.1"/></svg>(+555) 310-4482</div>
    <div class="footer-line small"><svg width="16" height="12" viewBox="0 0 16 12"><rect x=".6" y=".6" width="14.8" height="10.8" fill="none" stroke="#fff" stroke-width="1.1"/><path d="M.6.6L8 7l7.4-6.4" fill="none" stroke="#fff" stroke-width="1.1"/></svg>info@harlowmechanical.com</div>
  </div>
  <div class="footer-col" style="left:366px">
    <h4>Latest Tweet`s</h4>
    <div class="tweet">
      <span class="tweet-mark"></span>
      <p style="width:200px">Phasellus porta. Fusce susct varius mi. Cum sociis natoque penabus et magnis dis parturient montes, nasce-tur ridiculus mus. See more here http://hmc.link/x7Q2pd</p>
    </div>
  </div>
  <div class="footer-col" style="left:666px">
    <h4>Newsletter</h4>
    <p style="width:260px">Excepteur sint occaecat cupidatat non proident, sunt in culpa qui officia deserunt mollit anim</p>
    <div class="newsletter-form"><span class="field">Enter your email address</span><span class="submit">Sign Up</span></div>
  </div>
  <div class="footer-col" style="left:966px">
    <h4>Social Media</h4>
    <div class="social"><span aria-label="Social link"></span><span aria-label="Social link"></span><span aria-label="Social link"></span></div>
  </div>
</footer>
<div class="footer-bar">2016 &nbsp;All Rights Reserved.</div>

</body>
</html>
```